SaaS Early tech startup business card design

Unique design for experience ecommerce platform company. the business cards will be used by executive members. conformance with color code is required.

```html
<!DOCTYPE html>
<html lang="en">
<head>
<meta charset="utf-8">
<title>novra — business card</title>
<link rel="stylesheet" href="https://fonts.googleapis.com/css2?family=Montserrat:wght@500;600;700&family=Arimo:wght@400&display=swap">
<style>
  :root {
    --backdrop: #c9c9c9;
    --teal-deep: #05668f;
    --teal-mid: #0a8f9c;
    --teal-bright: #00b59c;
    --accent: #13a097;
    --ink: #2b2b2b;
    --card-white: #ffffff;
    --shadow: rgba(0, 0, 0, 0.28);
  }
  * { box-sizing: border-box; margin: 0; padding: 0; }
  html, body {
    width: 1200px; height: 900px; overflow: hidden;
    background: var(--backdrop);
  }
  .canvas {
    position: relative; width: 1200px; height: 900px;
    background: radial-gradient(circle at 50% 40%, #d6d6d6 0%, var(--backdrop) 55%, #b8b8b8 100%);
  }
  .card {
    position: absolute; width: 560px; height: 320px;
    border-radius: 26px; overflow: hidden;
    box-shadow: 0 10px 24px var(--shadow);
  }
  .card--front {
    left: 170px; top: 100px;
    background: linear-gradient(200deg, var(--teal-deep) 0%, var(--teal-mid) 45%, var(--teal-bright) 100%);
  }
  .card--back {
    left: 470px; top: 480px;
    background: var(--card-white);
  }
  .front-decoration {
    position: absolute; left: 300px; top: 30px; width: 230px; height: 260px;
    border-radius: 50%;
    background: radial-gradient(circle, rgba(255,255,255,0.07) 0%, rgba(255,255,255,0) 70%);
  }
  .back-decoration {
    position: absolute; left: 280px; top: 20px; width: 260px; height: 280px;
    border-radius: 50%;
    background: radial-gradient(circle, rgba(10,143,156,0.06) 0%, rgba(10,143,156,0) 70%);
  }
  .wordmark {
    font-family: "Montserrat", sans-serif; font-weight: 700;
    letter-spacing: -1px; line-height: 1;
  }
  .card--front .wordmark {
    position: absolute; left: 0; right: 0; top: 118px;
    text-align: center; font-size: 78px; color: #ffffff;
  }
  .card--back .wordmark {
    position: absolute; left: 40px; top: 40px;
    font-size: 84px; color: var(--teal-deep);
  }
  .person {
    position: absolute; left: 42px; top: 160px;
    font-family: "Montserrat", sans-serif;
  }
  .person__name {
    font-size: 21px; font-weight: 600; color: var(--accent);
    letter-spacing: 0.5px; text-transform: uppercase;
  }
  .person__role {
    font-family: "Arimo", sans-serif;
    font-size: 15px; color: var(--ink); margin-top: 2px;
  }
  .contact-list {
    list-style: none; margin-top: 12px;
    font-family: "Arimo", sans-serif; font-size: 15px; color: var(--ink);
  }
  .contact-list li {
    display: flex; align-items: center; gap: 8px; height: 22px;
  }
  .contact-list svg { width: 15px; height: 15px; flex: none; }
  .address {
    position: absolute; right: 34px; top: 150px;
    font-family: "Arimo", sans-serif; font-size: 14px; color: var(--ink);
    font-style: normal; text-align: right; line-height: 1.35;
  }
</style>
</head>
<body>
<main class="canvas">

  <section class="card card--front" aria-label="Card front">
    <div class="front-decoration" role="img" aria-label="Faint line-art brand motif"></div>
    <div class="wordmark">novra</div>
  </section>

  <section class="card card--back" aria-label="Card back">
    <div class="back-decoration" role="img" aria-label="Faint line-art brand motif"></div>
    <div class="wordmark">novra</div>

    <div class="person">
      <p class="person__name">Marcus Ellery</p>
      <p class="person__role">Managing Director</p>
      <ul class="contact-list">
        <li>
          <svg viewBox="0 0 16 16" aria-hidden="true"><path d="M3.5 1.5l2.5 0 1 3.5-1.6 1.2a8 8 0 0 0 4.4 4.4L11 9l3.5 1v2.5c0 1-1 2-2 2A11 11 0 0 1 1.5 3.5c0-1 1-2 2-2z" fill="var(--accent)"/></svg>
          021-555 304 118
        </li>
        <li>
          <svg viewBox="0 0 16 16" aria-hidden="true"><rect x="1" y="3" width="14" height="10" rx="1" fill="var(--accent)"/><path d="M1.5 3.8L8 9l6.5-5.2" fill="none" stroke="#fff" stroke-width="1.2"/></svg>
          hello@novrahq.com
        </li>
        <li>
          <svg viewBox="0 0 16 16" aria-hidden="true"><circle cx="8" cy="8" r="6.5" fill="none" stroke="var(--accent)" stroke-width="1.4"/><ellipse cx="8" cy="8" rx="2.8" ry="6.5" fill="none" stroke="var(--accent)" stroke-width="1.2"/><path d="M1.5 8h13M2.6 4.8h10.8M2.6 11.2h10.8" stroke="var(--accent)" stroke-width="1.1"/></svg>
          www.novrahq.com
        </li>
      </ul>
    </div>

    <address class="address">
      88 , Harbor Lane, Suite 4<br>
      30117, Westland
    </address>
  </section>

</main>
</body>
</html>
```